Volbrey Inc Business Card

Looking to get an updated business card for a Contract Machining company (www.volbreyinc.example) - looking for a clean design the portrays the technical nature of the business - colors can follow the website design and be in any combination that makes sense (red black, white, metallic or silver) - logos attached for use also. Would like space for: Name, title, business phone (555 214-3086), cell phone , website (www.volbreyinc.example) - possibly QR code could be integrated for website (designer choice), business address - 418 Harlow Bend, Alder Falls, OH 44199 (cards will be for 4 employees, I will either need to modify a template or I can provide individual information)
Target Market(s)
Aerospace, defense and medical device manufacturing companies that need machining
Industry/Entity Type
Machining for aerospace, defense, medical
Contact Information for Business Card
Name, Title, Business Phone, Cell Phone, email, business website and business address
Look and feel

```html
<!DOCTYPE html>
<html lang="en">
<head>
<meta charset="utf-8">
<title>Volbrey Inc Business Card</title>
<link rel="stylesheet" href="https://fonts.googleapis.com/css2?family=Arimo:wght@400;700&family=Montserrat:wght@700;800&display=swap">
<style>
  :root {
    --bg: #2a2a2c;
    --red: #b51f24;
    --ink: #2b2b2b;
    --grey: #6f6d6e;
    --muted: #8a8a8a;
    --white: #ffffff;
    --card-dark: #1c1c1d;
    --card-dark-2: #3a3a3c;
  }
  * { box-sizing: border-box; margin: 0; padding: 0; }
  html, body { width: 1200px; height: 874px; overflow: hidden; }
  body {
    background: var(--bg);
    font-family: "Arimo", Arial, sans-serif;
    display: flex; flex-direction: column; align-items: center; justify-content: center; gap: 34px;
  }
  .card {
    position: relative; width: 680px; height: 388px; border-radius: 20px; overflow: hidden;
    box-shadow: 0 14px 30px rgba(0,0,0,.45);
  }

  /* back */
  .card-back { background: var(--card-dark); }
  .card-back .pattern {
    position: absolute; inset: 0;
    background: linear-gradient(100deg, var(--card-dark) 0%, #262628 50%, var(--card-dark-2) 100%);
  }
  .back-brand {
    position: absolute; right: 60px; bottom: 56px;
    display: flex; flex-direction: column; align-items: center; gap: 8px;
  }
  .back-brand .mark { width: 86px; height: 86px; border-radius: 50%; background: var(--red); }
  .back-brand .wordmark {
    font-family: "Montserrat", sans-serif; font-weight: 800; font-size: 20px;
    color: var(--red); letter-spacing: .5px; white-space: nowrap;
  }

  /* front */
  .card-front { background: var(--white); }
  .brand {
    position: absolute; left: 50px; top: 50px; width: 220px;
    display: flex; flex-direction: column; align-items: center; gap: 12px;
  }
  .brand .mark { width: 140px; height: 140px; border-radius: 50%; background: var(--red); }
  .brand .wordmark {
    font-family: "Montserrat", sans-serif; font-weight: 800; font-size: 28px;
    color: var(--red); letter-spacing: .5px; white-space: nowrap;
  }
  .divider {
    position: absolute; left: 300px; top: 60px; width: 1px; height: 190px;
    background: linear-gradient(var(--white), #b7b7b7, var(--white));
  }
  .contact { position: absolute; left: 330px; top: 58px; color: var(--ink); }
  .contact .name {
    font-family: "Montserrat", sans-serif; font-weight: 800; font-size: 26px; color: var(--red);
  }
  .contact .title { font-size: 16px; color: var(--muted); margin-top: 2px; }
  .contact .address { font-size: 17px; line-height: 21px; margin-top: 16px; }
  .contact ul { list-style: none; margin-top: 10px; font-size: 17px; line-height: 22px; }
  .contact li { display: flex; align-items: center; gap: 10px; }
  .contact svg { width: 14px; height: 14px; fill: var(--red); flex: none; }

  .band-red {
    position: absolute; left: 0; top: 296px; width: 530px; height: 38px; background: var(--red);
    display: flex; align-items: center; padding-left: 100px;
  }
  .band-red .web { color: var(--white); font-size: 17px; letter-spacing: 3px; white-space: nowrap; }
  .band-grey {
    position: absolute; left: 530px; top: 306px; right: 0; height: 30px; background: var(--grey);
  }
  .band-dot {
    position: absolute; left: 508px; top: 298px; width: 44px; height: 44px; border-radius: 50%;
    background: var(--red); border: 3px solid var(--white);
  }
</style>
</head>
<body>
  <section class="card card-back">
    <div class="pattern" role="img" aria-label="Repeating embossed company mark pattern on black"></div>
    <div class="back-brand">
      <div class="mark"></div>
      <div class="wordmark">VOLBREY INC.</div>
    </div>
  </section>

  <section class="card card-front">
    <div class="brand">
      <div class="mark"></div>
      <div class="wordmark">VOLBREY INC.</div>
    </div>
    <div class="divider"></div>
    <div class="contact">
      <div class="name">Dale Markov</div>
      <div class="title">President</div>
      <div class="address">418 Harlow Bend<br>Alder Falls, OH 44199</div>
      <ul>
        <li><svg viewBox="0 0 24 24"><path d="M6.6 10.8a15.1 15.1 0 0 0 6.6 6.6l2.2-2.2a1 1 0 0 1 1-.25 11.4 11.4 0 0 0 3.6.57 1 1 0 0 1 1 1V20a1 1 0 0 1-1 1A17 17 0 0 1 3 4a1 1 0 0 1 1-1h3.5a1 1 0 0 1 1 1c0 1.25.2 2.450.57 3.57a1 1 0 0 1-.25 1z"/></svg>555 214-3086</li>
        <li><svg viewBox="0 0 24 24"><path d="M7 1h10a2 2 0 0 1 2 2v18a2 2 0 0 1-2 2H7a2 2 0 0 1-2-2V3a2 2 0 0 1 2-2zm0 3v14h10V4z"/></svg>555 630-7192</li>
        <li><svg viewBox="0 0 24 24"><path d="M2 5h20v14H2zm2 2v.5l8 5 8-5V7zm0 2.8V17h16V9.8l-8 5z"/></svg>info@volbreyinc.example</li>
      </ul>
    </div>
    <div class="band-red"><span class="web">www.volbreyinc.example</span></div>
    <div class="band-grey"></div>
    <div class="band-dot"></div>
  </section>
</body>
</html>
```